Im open to ideas.. I was thinking on my business cards aswell as my logo. a place for my name. email. phone number and abn..

ive attched a file with my business logo. which i dont love the colours.. i was think a dark background with charcoal letters so something along those colour schumes but im open to ideas..

BRM Constructions

```html
<!DOCTYPE html>
<html lang="en">
<head>
<meta charset="utf-8">
<title>BRM Constructions – Business Cards</title>
<link rel="stylesheet" href="https://fonts.googleapis.com/css2?family=Montserrat:wght@500;700&display=swap">
<style>
  :root {
    --backdrop: #e9e6e1;
    --card-dark: #1f1f21;
    --card-light: #ffffff;
    --brand-red: #e0141b;
    --ink-dark: #1b1b1d;
    --ink-light: #ffffff;
  }
  * { margin: 0; padding: 0; box-sizing: border-box; }
  html, body {
    width: 1200px;
    height: 950px;
    overflow: hidden;
    background: var(--backdrop);
    font-family: "Montserrat", Arial, sans-serif;
  }
  .canvas {
    position: relative;
    width: 1200px;
    height: 950px;
  }
  .card {
    position: absolute;
    width: 700px;
    height: 400px;
    overflow: hidden;
    box-shadow: 0 18px 40px rgba(0, 0, 0, 0.22);
  }
  .card--front {
    left: 130px;
    top: 50px;
    background: var(--card-dark);
  }
  .card--back {
    left: 370px;
    top: 500px;
    background: var(--card-light);
  }
  .wordmark {
    position: absolute;
    display: flex;
    align-items: center;
    gap: 14px;
    font-weight: 700;
    letter-spacing: 0.02em;
    white-space: nowrap;
  }
  .wordmark__square {
    width: 22px;
    height: 22px;
    background: var(--brand-red);
  }
  .card--front .wordmark {
    left: 50%;
    top: 50%;
    transform: translate(-50%, -50%);
    font-size: 44px;
    color: var(--ink-light);
  }
  .card--back .wordmark {
    right: 56px;
    top: 72px;
    font-size: 34px;
    color: var(--ink-dark);
  }
  .info-band {
    position: absolute;
    left: 0;
    bottom: 0;
    width: 100%;
    height: 168px;
    background: var(--brand-red);
  }
  .contact {
    position: absolute;
    left: 250px;
    top: 262px;
    color: var(--ink-light);
    font-weight: 500;
    font-size: 15px;
    line-height: 1.65;
  }
  .contact__name {
    font-size: 21px;
    font-weight: 700;
    margin-bottom: 4px;
  }
  .contact__role { font-weight: 500; }
</style>
</head>
<body>
  <main class="canvas">
    <section class="card card--front" aria-label="Business card front">
      <div class="wordmark">
        <span class="wordmark__square" aria-hidden="true"></span>
        <span class="wordmark__name">BRM Constructions</span>
      </div>
    </section>

    <section class="card card--back" aria-label="Business card back">
      <div class="wordmark">
        <span class="wordmark__square" aria-hidden="true"></span>
        <span class="wordmark__name">BRM Constructions</span>
      </div>

      <div class="info-band" aria-hidden="true"></div>

      <div class="contact">
        <p class="contact__name">Sam Carter - <span class="contact__role">President</span></p>
        <p class="contact__abn">ABN: 987 654 321</p>
        <p class="contact__lines">P : 555 0142 7781 &nbsp; E : sam@brmbuild.com</p>
      </div>
    </section>
  </main>
</body>
</html>
```